TLK Electricial Contracting Services

Hi guys, after a design for my small electrical company, have logo design files to be incorporated into the layout, the basic concept is electrical contracting services for residential, commercial, industrial & data services, image is clean clear and strong,

Card format is to have a nice clean logo on front,with maybe the Residential – commercial – industrial - data, followed with licensed & insured, followed by contact details on backside of the card.

Target Market(s)

Residential, commercial, industrial sectors.

Industry/Entity Type

Electrical

Contact Information for Business Card

TLK logo,
Residential – commercial – industrial - data
REC: 61307
Email: tlk@vornamail.net.au
Phone: 0487 352 019

Requirements
Must have
• Clean & strong design.
Nice to have
• If possible, I would like the logo colours inverted so the text is orange and the background is black on the front of the card, then the backside of the card be the reverse colour
Should not have
• No Sparks, lightning bolts,

```html
<!DOCTYPE html>
<html lang="en">
<head>
<meta charset="utf-8">
<title>TLK Electrical – Business Card</title>
<link rel="stylesheet" href="https://fonts.googleapis.com/css2?family=Exo+2:ital,wght@0,600;1,300&family=PT+Sans:wght@400&display=swap">
<style>
  :root {
    --ink: #0b0b0b;
    --orange: #f7801f;
    --stage: #ececec;
    --stage-light: #f7f7f7;
  }
  * { margin: 0; padding: 0; box-sizing: border-box; }
  html, body {
    width: 1200px;
    height: 521px;
    overflow: hidden;
  }
  body {
    position: relative;
    background: radial-gradient(ellipse at center, var(--stage-light) 0%, var(--stage) 75%);
    font-family: "Exo 2", sans-serif;
  }
  .card {
    position: absolute;
    top: 112px;
    width: 519px;
    height: 296px;
    box-shadow: 0 3px 8px rgba(0, 0, 0, 0.25);
    text-align: center;
  }
  .card--front { left: 61px; background: var(--ink); color: var(--orange); }
  .card--back  { left: 621px; background: var(--orange); color: var(--ink); }

  .brand-name {
    position: absolute;
    left: 0; right: 0;
    font-family: "Exo 2", sans-serif;
    font-weight: 600;
    line-height: 1;
    letter-spacing: 2px;
  }
  .card--front .brand-name { top: 63px; font-size: 84px; }
  .card--back .brand-name  { top: 41px; font-size: 60px; }

  .company-name {
    position: absolute;
    left: 0; right: 0;
    font-family: "Exo 2", sans-serif;
    font-weight: 600;
  }
  .card--front .company-name { top: 153px; font-size: 19px; letter-spacing: 0.3px; }
  .card--back .company-name  { top: 102px; font-size: 12.5px; }

  .services-blurb {
    position: absolute;
    left: 0; right: 0;
    top: 202px;
    font-family: "Exo 2", sans-serif;
    font-style: italic;
    font-weight: 300;
    font-size: 16px;
    line-height: 20px;
  }

  .contact {
    position: absolute;
    left: 0; right: 0;
    font-family: "PT Sans", sans-serif;
    font-size: 18px;
    line-height: 20px;
  }
  .contact--sectors { top: 148px; }
  .contact--details { top: 203px; }
</style>
</head>
<body>
  <section class="card card--front" aria-label="Card front">
    <p class="brand-name">TLK</p>
    <p class="company-name">Tolan Kerr Electrical</p>
    <p class="services-blurb">Electrical contracting services for residential,<br>commercial, industrial &amp; data services.</p>
  </section>

  <section class="card card--back" aria-label="Card back">
    <p class="brand-name">TLK</p>
    <p class="company-name">Tolan Kerr Electrical</p>
    <div class="contact contact--sectors">
      <p>Residential – Commercial – Industrial – Data</p>
      <p>REC: 61307</p>
    </div>
    <div class="contact contact--details">
      <p>E-mail: tlk@vornamail.net.au</p>
      <p>Phone: 0487.352.019</p>
    </div>
  </section>
</body>
</html>
```